Business Card Design for Marketing Firm

Looking for business card design for higher end marketing firm. Clean but impressionable/trendy. We are a marketing firm that represents manufacturers in the foodservice equipment and supply industry. Our customers are end users such has hotels, restaurants, country clubs, convention centers and casinos as well as distributors of restaurants supplies and equipment, and manufacturers of foodservice equipment and supplies.
Target Market(s)
Hotels, Restaurants, Supply & Equipment Distributors, Foodservice Manufacturers
Industry/Entity Type
Foodservice/Hospitality
Contact Information for Business Card
Name, Title, Contact Number, Email, Website, Social Media, Address
Requirements
Must have
- Clean & Simple but Serious and Impressionable

```html
<!DOCTYPE html>
<html lang="en">
<head>
<meta charset="UTF-8">
<title>Meridian Service Reps – Business Card</title>
<link rel="stylesheet" href="https://fonts.googleapis.com/css2?family=Cinzel:wght@400;700&family=Arimo:wght@400&display=swap">
<style>
  :root {
    --navy: #0b0b7e;
    --navy-deep: #06066f;
    --navy-soft: #3a3ab8;
    --paper: #f5f5f7;
    --ink: #1b1b2a;
    --muted: #55556a;
    --backdrop: #d9d9de;
  }
  * { margin: 0; padding: 0; box-sizing: border-box; }
  html, body { width: 1200px; height: 960px; overflow: hidden; }
  body { background: var(--backdrop); position: relative; font-family: "Arimo", Arial, sans-serif; }

  .card {
    position: absolute; left: 250px; width: 700px; height: 400px;
    border-radius: 24px; overflow: hidden;
    box-shadow: 0 8px 24px rgba(0,0,0,.18);
  }

  /* Back */
  .card-back { top: 50px; background: var(--navy-deep); }
  .back-mark {
    position: absolute; inset: 0;
    display: flex; flex-direction: column; align-items: center; justify-content: center; gap: 18px;
  }
  .back-mark .dot { width: 90px; height: 90px; border-radius: 50%; background: var(--navy-soft); }
  .back-mark .wordmark {
    font-family: "Cinzel", Georgia, serif; font-weight: 400; font-size: 38px;
    letter-spacing: 2px; color: var(--navy-soft); text-align: center; line-height: 1.1;
  }

  /* Front */
  .card-front { top: 510px; background: var(--paper); color: var(--ink); }
  .front-brand {
    position: absolute; left: 40px; top: 38px;
    font-family: "Cinzel", Georgia, serif; font-weight: 400; font-size: 20px;
    color: var(--navy); letter-spacing: .5px; line-height: 1.2;
  }

  .person { position: absolute; left: 40px; top: 106px; }
  .person .name {
    font-family: "Cinzel", Georgia, serif; font-weight: 700; font-size: 27px; color: var(--navy);
    letter-spacing: .5px; line-height: 1.2;
  }
  .person .title { font-size: 15px; color: var(--muted); margin-top: 2px; }

  .address { position: absolute; left: 40px; top: 196px; font-size: 17px; line-height: 1.3; color: var(--ink); font-style: normal; }

  .contacts { position: absolute; left: 40px; top: 262px; list-style: none; font-size: 17px; line-height: 1.45; }
  .contacts li { display: flex; align-items: center; gap: 10px; }
  .contacts svg { width: 14px; height: 14px; fill: var(--navy); flex: none; }

  .social { position: absolute; right: 36px; top: 110px; display: flex; gap: 8px; }
  .social span { width: 24px; height: 24px; border-radius: 50%; background: var(--navy); }

  .front-mark {
    position: absolute; left: 380px; top: 190px; width: 290px;
    display: flex; align-items: center; gap: 14px;
  }
  .front-mark .dot { width: 46px; height: 46px; border-radius: 50%; background: var(--navy); flex: none; }
  .front-mark .wordmark {
    font-family: "Cinzel", Georgia, serif; font-weight: 400; font-size: 40px;
    color: var(--navy); letter-spacing: 1px;
  }
</style>
</head>
<body>

<section class="card card-back" aria-label="Card back">
  <div class="back-mark">
    <span class="dot" aria-hidden="true"></span>
    <p class="wordmark">Meridian Service Reps</p>
  </div>
</section>

<section class="card card-front" aria-label="Card front">
  <p class="front-brand">Meridian Service Reps</p>

  <div class="person">
    <h1 class="name">Owen Carter</h1>
    <p class="title">President</p>
  </div>

  <address class="address">
    2716 Harborview Lane<br>
    Glen Cove, NY 11542
  </address>

  <ul class="contacts">
    <li>
      <svg viewBox="0 0 24 24" aria-hidden="true"><path d="M6.6 10.8a15.1 15.1 0 0 0 6.6 6.6l2.2-2.2c.3-.3.7-.4 1-.2 1.1.4 2.3.6 3.6.6.6 0 1 .4 1 1V20c0 .6-.4 1-1 1A17 17 0 0 1 3 4c0-.6.4-1 1-1h3.5c.6 0 1 .4 1 1 0 1.3.2 2.5.6 3.6.1.3 0 .7-.2 1z"/></svg>
      (555) 0142-7788
    </li>
    <li>
      <svg viewBox="0 0 24 24" aria-hidden="true"><path d="M2 5h20v14H2z M2 5l10 8 10-8" stroke="#f5f5f7" stroke-width="1.5"/></svg>
      name@MERIDIAN.com
    </li>
    <li>
      <svg viewBox="0 0 24 24" aria-hidden="true"><circle cx="12" cy="12" r="10"/></svg>
      www.MERIDIAN.com
    </li>
  </ul>

  <div class="social" aria-label="Social media">
    <span></span><span></span><span></span>
  </div>

  <div class="front-mark">
    <span class="dot" aria-hidden="true"></span>
    <span class="wordmark">Meridian</span>
  </div>
</section>

</body>
</html>
```